Visitenkarten-Design für Pflegedienst
Zielgruppe
Pflegedienst
Aufgabenstellung
Siehe Beispielvisitenkarte. Es soll so ähnlich designt werden mit hochwertigem Papier. Die Angaben darauf sind auch schon korrekt.

```html
<!DOCTYPE html>
<html lang="de">
<head>
<meta charset="utf-8">
<title>Visitenkarte Atemhafen24</title>
<link href="https://fonts.googleapis.com/css2?family=Open+Sans:wght@400;600;700&display=swap" rel="stylesheet">
<style>
:root{
  --bg:#e6e7ea;
  --card:#ffffff;
  --blue:#34558f;
  --red:#d3202a;
  --ink:#2b2b2b;
  --photo-a:#e9e6e3;
  --photo-b:#c9b3a4;
}
*{box-sizing:border-box;margin:0;padding:0}
html,body{width:1200px;height:978px;overflow:hidden;background:var(--bg);font-family:"Open Sans",Arial,sans-serif}
.stage{position:relative;width:1200px;height:978px}
.card{position:absolute;left:260px;width:680px;height:400px;background:var(--card);overflow:hidden;box-shadow:0 6px 18px rgba(0,0,0,.18)}
.card--front{top:45px}
.card--back{top:533px}
.band{position:absolute;left:0;width:100%;height:34px;background:var(--blue);color:#fff;font-size:17px;line-height:34px;letter-spacing:.3px}
.card--front .band{top:300px;padding-left:220px}
.card--back .band{top:322px;padding-left:210px}
.brand{position:absolute;display:flex;align-items:center}
.brand__mark{width:var(--m);height:var(--m);border-radius:50%;background:var(--red)}
.brand__rule{width:1px;background:var(--blue);margin:0 16px}
.brand__name{color:var(--blue);font-weight:400;letter-spacing:1px;line-height:1}
.brand__tag{color:var(--red);letter-spacing:.6px;margin-top:4px}
.card--front .brand{left:150px;top:100px;--m:78px}
.card--front .brand__rule{height:100px}
.card--front .brand__name{font-size:44px}
.card--front .brand__tag{font-size:19px}
.card--back .brand{left:34px;top:52px;--m:52px}
.card--back .brand__rule{height:68px;margin:0 12px}
.card--back .brand__name{font-size:30px}
.card--back .brand__tag{font-size:13px}
.person{position:absolute;left:40px;top:140px}
.person__name{color:var(--blue);font-weight:700;font-size:25px}
.person__role{color:var(--ink);font-size:15px;margin-top:2px}
.contacts{position:absolute;left:40px;top:210px;list-style:none;font-size:15px;color:var(--ink)}
.contacts li{display:flex;align-items:center;height:21px}
.contacts svg{width:15px;height:15px;margin-right:12px;fill:none;stroke:var(--blue);stroke-width:1.8}
.address{position:absolute;left:67px;top:300px;font-size:15px;color:var(--ink);line-height:1}
.address span{display:block}
.photo{position:absolute;right:0;top:0;width:230px;height:322px;background:linear-gradient(160deg,var(--photo-a) 0%,var(--photo-b) 45%,#f4f4f4 75%)}
</style>
</head>
<body>
<main class="stage">
  <section class="card card--front">
    <div class="brand">
      <span class="brand__mark"></span>
      <span class="brand__rule"></span>
      <div>
        <div class="brand__name">ATEMHAFEN24 GMBH</div>
        <div class="brand__tag">AUSSERKLINISCHE INTENSIVPFLEGE</div>
      </div>
    </div>
    <div class="band">www.atemhafen24.de</div>
  </section>

  <section class="card card--back">
    <div class="photo" role="img" aria-label="Porträtfoto des Geschäftsführers im weißen Hemd"></div>
    <div class="brand">
      <span class="brand__mark"></span>
      <span class="brand__rule"></span>
      <div>
        <div class="brand__name">ATEMHAFEN24 GMBH</div>
        <div class="brand__tag">AUSSERKLINISCHE INTENSIVPFLEGE</div>
      </div>
    </div>
    <div class="person">
      <div class="person__name">Jonas Weidmark LL.M.</div>
      <div class="person__role">Wirtschaftsjurist / Geschäftsführer</div>
    </div>
    <ul class="contacts">
      <li><svg viewBox="0 0 16 16"><rect x="4" y="1.5" width="8" height="13" rx="1.5"/><line x1="7" y1="12" x2="9" y2="12"/></svg>+49 151 20418836</li>
      <li><svg viewBox="0 0 16 16"><path d="M3 2l3 1 1 3-2 1.5a8 8 0 0 0 3.5 3.5L10 9l3 1 1 3-2 1.5C7 14 2 9 1.5 4z"/></svg>+49 7031 4092700</li>
      <li><svg viewBox="0 0 16 16"><rect x="2" y="6" width="12" height="7" rx="1"/><rect x="4.5" y="2" width="7" height="4"/><line x1="5" y1="10" x2="11" y2="10"/></svg>+49 7031 4092702</li>
      <li><svg viewBox="0 0 16 16"><rect x="1.5" y="3.5" width="13" height="9"/><path d="M1.5 3.5L8 9l6.5-5.5"/></svg>jw@atemhafen24.de</li>
    </ul>
    <div class="address"><span>Atemhafen24 GmbH</span></div>
    <div class="address" style="top:318px;display:none"></div>
    <div class="band">www.atemhafen24.de</div>
    <div class="address" style="top:300px;left:67px;display:none"></div>
  </section>
</main>
<style>
.card--back .address{top:296px}
.card--back .contacts{top:204px}
.card--back .address span{margin-bottom:4px}
</style>
</body>
</html>
```